Brief 1.
An Overview / Background of the Business & Services-
It is a new business being set up. Our business is to design a solution to enable Alumni of higher institutions in Nigeria apply for their academic transcript through our system. the name of our product will be Record Relay Nigeria. We need logo, site banner, advert banner and several academic images. See www.rrly-ng.example for more insight.
The Target Market / Audience you are trying to reach-
Alumni of Nigeria Universities, usually between the ages of 20-40.
Design Specifics; any preferences or ideas for Style, Colour, Imagery, etc-
Color scheme will be several shades of light blue and white. Please check www.rrly-ng.example for more insight.

Brief 2

Pantrybasket.com is an online food and grocery shop, we supply fresh food stuff and other daily essential needs on request to customers. The site is already up (www.pantrybasket.example). We need logo, site rolling banner, advert banner and several offer graphics as shown in the placeholder images in the site now.
Working women in Nigeria.
Color scheme will be several shades of light Green and White. Please check the site.

```html
<!DOCTYPE html>
<html lang="en">
<head>
<meta charset="utf-8">
<title>Pantry Basket – Grocery Shop</title>
<link href="https://fonts.googleapis.com/css2?family=Open+Sans:wght@400;600;700&family=Oswald:wght@400;500;600&display=swap" rel="stylesheet">
<style>
:root{
  --green:#8dc63f;
  --green-dark:#6fae2a;
  --teal:#2fae91;
  --promo:#3cae8e;
  --price:#4caf50;
  --ink:#222;
  --muted:#555;
  --line:#cfcfcf;
  --footer:#e6f0cc;
  --panel:#f4f4f4;
  --black:#111;
  --heart:#e53935;
}
*{box-sizing:border-box;margin:0;padding:0}
html,body{width:886px;height:1200px;overflow:hidden;background:#fff}
body{position:relative;font-family:"Open Sans",sans-serif;color:var(--ink);font-size:9px}
.abs{position:absolute}
.brand{left:112px;top:8px;display:flex;align-items:center;gap:8px}
.brand-mark{width:56px;height:56px;border-radius:50%;background:var(--green)}
.brand-name{font-family:"Oswald",sans-serif;font-weight:600;font-size:27px;color:var(--teal);line-height:1}
.brand-slogan{font-size:10px;color:#333;margin-top:3px}
.search{left:384px;top:8px;width:82px;height:17px;border:1px solid #bbb;font-size:8px;color:#444;padding:3px 0 0 14px}
.search svg{position:absolute;left:4px;top:4px}
.toplinks{left:486px;top:10px;display:flex;gap:10px;font-size:8.5px;color:#333}
.toplinks span::before{content:"▸";font-size:7px;margin-right:2px}
.toplinks span+span{border-left:1px solid #ccc;padding-left:8px}
.login{left:731px;top:7px;width:43px;height:18px;background:var(--teal);color:#fff;font-size:8.5px;font-weight:700;text-align:center;line-height:18px}
.info{display:flex;gap:6px;align-items:center;font-size:8.5px;line-height:1.25;color:#333}
.info small{font-size:7.5px}
.cartinfo b{font-size:8px}
.cartinfo .amt{color:var(--green);font-weight:700;font-size:8px}
.nav{left:112px;top:86px;width:662px;height:27px;background:var(--green);display:flex;align-items:center}
.nav span{color:#fff;font-family:"Oswald",sans-serif;font-size:11px;letter-spacing:.4px;padding:0 15px;border-right:1px solid rgba(255,255,255,.5);line-height:16px}
.nav span:last-child{border:none}
.hero{left:112px;top:117px;width:662px;height:273px;background:radial-gradient(ellipse at 55% 55%,#f2a23c 0%,#d9343a 35%,#8b2a4a 60%,#e9e2e2 85%);border:1px solid #ddd}
.hero-label{left:112px;top:315px;width:150px;height:31px;background:var(--black);color:#fff;font-family:"Oswald",sans-serif;font-size:13px;text-align:center;line-height:31px;letter-spacing:.5px}
.arrow{width:32px;height:32px;border-radius:50%;background:var(--black)}
.box{background:#fff;box-shadow:0 2px 4px rgba(0,0,0,.18);border:1px solid #eee}
.tab{background:var(--teal);color:#fff;font-size:9.5px;font-weight:600;height:18px;line-height:18px;padding:0 13px;letter-spacing:.2px}
.catlist{left:128px;top:428px;width:155px}
.catlist li{list-style:none;height:24px;line-height:24px;border-bottom:1px solid var(--line);font-size:8.5px;position:relative}
.catlist li.sub::after{content:"›";position:absolute;right:0;color:var(--teal);font-size:13px;top:-1px}
.cart-msg{left:128px;top:654px;width:130px;font-size:8.5px;line-height:14px}
.recent{left:126px;width:157px;height:56px;border:1px solid #ccc}
.recent .thumb{position:absolute;left:8px;top:10px;width:36px;height:24px}
.recent .title{position:absolute;left:52px;top:6px;font-size:8.5px;line-height:13px}
.recent .rule{position:absolute;left:52px;right:6px;top:34px;border-top:1px solid #ccc}
.recent .add{position:absolute;left:53px;top:39px;font-size:8px;color:var(--teal);font-weight:600;letter-spacing:.3px}
.promo{left:308px;top:397px;width:466px;height:135px;background:linear-gradient(#fff,#f1f1f1);border:1px solid #ddd;box-shadow:0 2px 4px rgba(0,0,0,.15)}
.promo-img{left:318px;top:403px;width:158px;height:120px;background:radial-gradient(circle at 50% 55%,#c48a3c,#e6b04c 45%,#f3f3f3 72%)}
.promo-h1{left:449px;top:416px;font-family:"Oswald",sans-serif;font-weight:500;color:var(--promo);font-size:19px;letter-spacing:.2px}
.promo-sub{left:450px;top:441px;font-size:9.5px;width:309px;border-bottom:1px solid #ccc;padding-bottom:4px}
.promo-h2{left:554px;top:467px;font-family:"Oswald",sans-serif;font-weight:500;color:var(--promo);font-size:19px}
.readmore{left:699px;top:496px;width:56px;height:16px;background:var(--black);color:#fff;font-size:8px;text-align:center;line-height:16px}
.panel{left:309px;top:548px;width:465px;height:484px;background:var(--panel)}
.card{width:133px;height:212px;background:#fff;border:2px solid #ddd}
.card .img{position:absolute;left:0;top:0;right:0;height:120px}
.card .name{position:absolute;left:9px;top:134px;font-size:9.5px;font-weight:600;color:#222}
.card .price{position:absolute;left:9px;top:148px;font-size:11px;color:var(--price)}
.card .btn{position:absolute;left:9px;top:161px;width:60px;height:19px;background:var(--green);color:#fff;font-size:8px;font-weight:700;text-align:center;line-height:19px}
.card .wish{position:absolute;left:11px;top:191px;font-size:8px;color:#333}
.card .wish::before{content:"♥";color:var(--heart);margin-right:3px}
.footer{left:112px;top:1049px;width:662px;height:151px;background:var(--footer)}
.fcol{top:1066px}
.fcol h4{font-size:9.5px;font-weight:600;margin-bottom:10px;letter-spacing:.2px}
.fcol p{font-size:8px;height:19px}
.soc{display:flex;align-items:center;gap:6px}
.soc i{width:12px;height:12px;border-radius:2px;background:var(--teal);display:inline-block}
.cards{display:flex;gap:6px}
.cards i{width:28px;height:16px;border:1px solid #bbb;background:#fff;display:inline-block}
.cards i:nth-child(3){background:#2f4f9a}
.frule{left:130px;top:1172px;width:634px;border-top:1px solid #b9c69c}
.fbottom{left:134px;top:1181px;font-size:8px}
.copy{right:124px;top:1181px;font-size:8px}
</style>
</head>
<body>

<header>
  <div class="abs brand">
    <span class="brand-mark"></span>
    <div><div class="brand-name">Pantry Basket</div><div class="brand-slogan">slogan here</div></div>
  </div>
  <div class="abs search"><svg width="8" height="8" viewBox="0 0 8 8"><circle cx="3.2" cy="3.2" r="2.4" fill="none" stroke="#666"/><line x1="5" y1="5" x2="7.5" y2="7.5" stroke="#666"/></svg>Search</div>
  <div class="abs toplinks"><span>My Account</span><span>My Wishlist</span><span>My Cart</span><span>Checkout</span></div>
  <div class="abs login">LOGIN</div>

  <div class="abs info" style="left:382px;top:42px">
    <svg width="20" height="20" viewBox="0 0 20 20"><path d="M4 3c2-1 3 3 2 4-1 1 2 5 4 6 1-1 4 0 4 2-1 3-5 2-8-1S2 5 4 3z" fill="#333"/><circle cx="14" cy="5" r="4" fill="#4a90d9"/></svg>
    <div>Give us Call<br>1-800-Pantry(1-800-726-8790)</div>
  </div>
  <div class="abs info" style="left:551px;top:44px">
    <svg width="24" height="18" viewBox="0 0 24 18"><rect x="1" y="3" width="14" height="10" fill="#e53935"/><path d="M15 6h5l3 4v3h-8z" fill="#555"/><circle cx="5" cy="15" r="2" fill="#333"/><circle cx="19" cy="15" r="2" fill="#333"/></svg>
    <div>Free Shipping<br><small>On order Over $30 offer today</small></div>
  </div>
  <div class="abs info cartinfo" style="left:712px;top:43px">
    <svg width="22" height="20" viewBox="0 0 22 20"><path d="M1 2h4l3 11h11l2-8H7" fill="none" stroke="#333" stroke-width="1.6"/><circle cx="9" cy="17" r="1.6" fill="#333"/><circle cx="17" cy="17" r="1.6" fill="#333"/></svg>
    <div><b>(0) ITEMS</b><br><span class="amt">$0.00</span></div>
  </div>
</header>

<nav class="abs nav">
  <span>ALL</span><span>HEALTH &amp; WELLNESS</span><span>FRUITS &amp; VEGS</span><span>POULTRY, MEAT &amp; FISH</span><span>FOOD STUFFS</span><span>RECIPES</span><span>OTHERS</span>
</nav>

<section>
  <div class="abs hero" role="img" aria-label="Glass bowl of mixed fresh fruit with strawberries and berries"></div>
  <div class="abs hero-label">GROCERY SHOPPING</div>
  <svg class="abs arrow" style="left:135px;top:232px" viewBox="0 0 32 32"><circle cx="16" cy="16" r="16" fill="#111"/><path d="M18 10l-6 6 6 6" stroke="#fff" stroke-width="2.2" fill="none"/></svg>
  <svg class="abs arrow" style="left:720px;top:232px" viewBox="0 0 32 32"><circle cx="16" cy="16" r="16" fill="#111"/><path d="M14 10l6 6-6 6" stroke="#fff" stroke-width="2.2" fill="none"/></svg>
</section>

<aside>
  <div class="abs box" style="left:112px;top:398px;width:185px;height:208px"></div>
  <div class="abs tab" style="left:109px;top:405px">CATEGORIES</div>
  <ul class="abs catlist">
    <li>All</li><li>Health &amp; Wellness</li><li class="sub">Fruits &amp; Vegs</li><li class="sub">Poultry, Meat &amp; Fish</li><li class="sub">Food Stuffs</li><li>Recipes</li><li class="sub" style="border:none">Others</li>
  </ul>

  <div class="abs box" style="left:112px;top:620px;width:185px;height:74px"></div>
  <div class="abs tab" style="left:109px;top:627px">CATEGORIES</div>
  <p class="abs cart-msg">You have no items in your shopping cart.</p>

  <div class="abs box" style="left:112px;top:709px;width:185px;height:305px"></div>
  <div class="abs tab" style="left:109px;top:717px">RECENT PRODUCTS</div>
  <div class="abs recent" style="top:747px"><div class="thumb" role="img" aria-label="Frozen tilapia fish" style="background:#6f7f8a"></div><div class="title">Frozen Tilapia (1kg)<br>$56.99</div><div class="rule"></div><div class="add">ADD TO CART</div></div>
  <div class="abs recent" style="top:811px"><div class="thumb" role="img" aria-label="Red snapper fish" style="background:#e39a8f"></div><div class="title">Red Snapper (1kg)<br>$56.99</div><div class="rule"></div><div class="add">ADD TO CART</div></div>
  <div class="abs recent" style="top:876px"><div class="thumb" role="img" aria-label="Frozen croacker fish" style="background:#9aa19a"></div><div class="title">Frozen Croacker (1kg)<br>$56.99</div><div class="rule"></div><div class="add">ADD TO CART</div></div>
  <div class="abs recent" style="top:942px"><div class="thumb" role="img" aria-label="Titus fish" style="background:#8d9bb0"></div><div class="title">Titus (1kg)<br>$56.99</div><div class="rule"></div><div class="add">ADD TO CART</div></div>
</aside>

<section>
  <div class="abs promo"></div>
  <div class="abs promo-img" role="img" aria-label="Wicker basket of fresh vegetables"></div>
  <div class="abs promo-h1">FREE DELIVERY &amp; GET 10% DISCOUNT</div>
  <div class="abs promo-sub">ON EVERY REGISTERS USERS</div>
  <div class="abs promo-h2">HURRY OFFER ENDS SOON</div>
  <div class="abs readmore">Read More</div>
</section>

<main>
  <div class="abs panel"></div>
  <div class="abs tab" style="left:306px;top:553px">LATEST PRODUCTS</div>

  <div class="abs card" style="left:325px;top:584px"><div class="img" role="img" aria-label="Paper bag of groceries and vegetables" style="background:linear-gradient(#f5f5f5,#c9a27a)"></div><div class="name">Donec Semper</div><div class="price">$34.00</div><div class="btn">Add to Cart</div><div class="wish">Add to Wishlist</div></div>
  <div class="abs card" style="left:473px;top:584px"><div class="img" role="img" aria-label="Olive oil, olives and pasta" style="background:linear-gradient(#f5f5f5,#d6b650)"></div><div class="name">Curabitur Dolor</div><div class="price">$52.00</div><div class="btn">Add to Cart</div><div class="wish">Add to Wishlist</div></div>
  <div class="abs card" style="left:625px;top:584px"><div class="img" role="img" aria-label="Fresh green pea pods" style="background:linear-gradient(#f5f5f5,#7dbb3a)"></div><div class="name">Phasellus Sit</div><div class="price">$20.00</div><div class="btn">Add to Cart</div><div class="wish">Add to Wishlist</div></div>

  <div class="abs card" style="left:325px;top:808px"><div class="img" role="img" aria-label="Sacks of nuts, beans and tomatoes" style="background:linear-gradient(#f5f5f5,#cfa56f)"></div><div class="name">Etiam Tristique</div><div class="price">$34.00</div><div class="btn">Add to Cart</div><div class="wish">Add to Wishlist</div></div>
  <div class="abs card" style="left:473px;top:808px"><div class="img" role="img" aria-label="Cabbage, peppers and cauliflower" style="background:linear-gradient(#cde2a8,#d9433a)"></div><div class="name">Ectus Arcu</div><div class="price">$52.00</div><div class="btn">Add to Cart</div><div class="wish">Add to Wishlist</div></div>
  <div class="abs card" style="left:625px;top:808px"><div class="img" role="img" aria-label="Red, green and yellow bell peppers" style="background:linear-gradient(90deg,#d8302a,#2f7d2a,#f0a31f)"></div><div class="name">Integer Tempor</div><div class="price">$20.00</div><div class="btn">Add to Cart</div><div class="wish">Add to Wishlist</div></div>
</main>

<footer>
  <div class="abs footer"></div>
  <div class="abs fcol" style="left:130px"><h4>CUSTOMER SERVICE</h4><p>About Us</p><p>Delivery Information</p><p>Privacy Policy</p><p>Term &amp; Condition</p></div>
  <div class="abs fcol" style="left:277px"><h4>MY ACCOUNT</h4><p>My Product</p><p>My Orders</p><p>My Address</p><p>My Personal Info</p></div>
  <div class="abs fcol" style="left:412px"><h4>FOLLOW ME</h4><p class="soc"><i></i>Friendspace</p><p class="soc"><i></i>Chirpline</p></div>
  <div class="abs fcol" style="left:527px"><h4>PAYMENT OPTIONS</h4><div class="cards"><i></i><i></i><i></i><i></i></div></div>
  <div class="abs frule"></div>
  <div class="abs fbottom">Site Map &nbsp;| &nbsp;Search Terms &nbsp;| &nbsp;Advanced Search &nbsp;| &nbsp;Orders and Returns &nbsp;| &nbsp;Contact Us</div>
  <div class="abs copy">© 2014 Pantrybasket.com Ltd</div>
</footer>

</body>
</html>
```